Bramblewick Forage Business Cards

I need a business card with my logo, number, Facebook account, and some information about what I am selling. Green card with logo on the front. 555-214-8392 phone number, @bramblewickforage Facebook, •Orchardgrass Hay •Alfalfa Hay •Mixed Grass Hay , and “Premium Quality Hay” all written on the back.

Target Market(s)

Hay

Contact Information for Business Card

Phone number, Facebook, different types of hay.

Colors
00AB8E
00BBA5
67D7C9
C6EFE9
E9F9F6

```html
<!DOCTYPE html>
<html lang="en">
<head>
<meta charset="utf-8">
<title>Bramblewick Forage Business Cards</title>
<link href="https://fonts.googleapis.com/css2?family=Roboto:ital,wght@0,400;0,700;1,400&display=swap" rel="stylesheet">
<style>
  :root {
    --page: #e4e4e4;
    --card-white: #ffffff;
    --brand-green: #00a859;
    --brand-green-light: #00b86a;
    --ink: #0d0d0d;
    --card-dark: #1c1c1d;
    --card-dark-edge: #2e2f31;
    --text-light: #ffffff;
  }
  * { margin: 0; padding: 0; box-sizing: border-box; }
  html, body { width: 1200px; height: 1200px; overflow: hidden; background: var(--page); }
  .stage {
    position: absolute; left: 0; top: 0;
    width: 1400px; height: 1400px;
    transform: scale(0.857143); transform-origin: 0 0;
    font-family: "Roboto", Arial, sans-serif;
  }
  .card {
    position: absolute; left: 306px; width: 800px; height: 456px;
    border-radius: 26px; overflow: hidden;
  }
  .card-front { top: 193px; background: var(--card-white); }
  .card-back {
    top: 762px;
    background: linear-gradient(160deg, var(--card-dark) 0%, var(--card-dark) 55%, var(--card-dark-edge) 100%);
  }
  .front-wave { position: absolute; inset: 0; width: 800px; height: 456px; }
  .brand-lockup {
    position: absolute; display: flex; align-items: center; gap: 16px;
  }
  .brand-mark { width: 40px; height: 40px; border-radius: 50%; flex: none; }
  .brand-name { font-weight: 700; line-height: 1.1; }
  .card-front .brand-lockup { left: 80px; top: 120px; }
  .card-front .brand-mark { background: var(--brand-green); }
  .card-front .brand-name { font-size: 40px; color: var(--brand-green); }
  .front-contact { position: absolute; left: 466px; top: 326px; color: var(--text-light); }
  .phone { font-weight: 700; font-size: 46px; letter-spacing: 0.5px; line-height: 1; }
  .social { display: flex; align-items: center; gap: 10px; margin-top: 8px; font-size: 29px; font-style: italic; }
  .social-dot { width: 36px; height: 36px; border-radius: 50%; background: var(--text-light); }
  .card-back .brand-lockup { left: 120px; top: 150px; }
  .card-back .brand-mark { width: 64px; height: 64px; background: var(--brand-green); }
  .card-back .brand-name { font-size: 44px; color: var(--text-light); }
  .back-phone { position: absolute; left: 313px; top: 240px; color: var(--text-light); font-size: 50px; }
  .product-list {
    position: absolute; left: 0; right: 0; top: 380px;
    text-align: center; color: var(--text-light); font-size: 18px; letter-spacing: 0.2px;
  }
  .product-list .sep {
    display: inline-block; width: 7px; height: 7px; border-radius: 50%;
    background: var(--brand-green); margin: 0 6px; vertical-align: middle;
  }
</style>
</head>
<body>
<main class="stage">
  <section class="card card-front">
    <svg class="front-wave" viewBox="0 0 800 456" aria-hidden="true">
      <defs>
        <linearGradient id="greenFill" x1="0" y1="1" x2="1" y2="0">
          <stop offset="0" stop-color="#00a04f"/>
          <stop offset="1" stop-color="#00b86a"/>
        </linearGradient>
      </defs>
      <path d="M0,305 C110,395 240,430 390,352 C480,305 540,232 610,214 C545,240 485,315 392,372 C250,450 110,425 0,338 Z" fill="var(--ink)"/>
      <path d="M0,348 C120,430 250,445 400,372 C500,320 560,220 660,218 C720,217 770,245 800,278 L800,456 L0,456 Z" fill="url(#greenFill)"/>
    </svg>
    <div class="brand-lockup">
      <span class="brand-mark"></span>
      <span class="brand-name">Bramblewick<br>Forage</span>
    </div>
    <div class="front-contact">
      <div class="phone">555-214-8392</div>
      <div class="social"><span class="social-dot"></span><span>@bramblewickforage</span></div>
    </div>
  </section>

  <section class="card card-back">
    <div class="brand-lockup">
      <span class="brand-mark"></span>
      <span class="brand-name">Bramblewick Forage</span>
    </div>
    <div class="phone back-phone">555-214-8392</div>
    <p class="product-list">Orchardgrass Hay<span class="sep"></span>Alfalfa Hay<span class="sep"></span>Mixed Grass Hay, &amp; Premium Quality Hay</p>
  </section>
</main>
</body>
</html>
```